Probate (Legal) Wordpress Design with Coding for Online Company

I need a Wordpress design with coding, pictures, content to be provided by me, fully responsive, and development. This is for a 6-7 page design.

Pages Needed: Home/About/Probate/Process/FAQ/Contact Us/Blog.

The home page should be organized as followed:
-Steps in Probate: Gather; Implement; Close (each step will come with content)
-Flat-Fee Price & Savings: Content will go here with a button to contact us (phone number) or just the phone number.
-You Have Questions, We Have Answers: five questions with content. Only one question answer to show at a time when clicked on the question from the list.
-Get to Know Us: a brief description with content about what we do and who we are.

Main image slogan: Helping Californians deal with loss with DIGNITY & UNDERSTATING (you may use a better slogan if you wish).

The Contact page should not have a map since we are an online company. We service the entire state of California in every county and city.

The About page should be simple, direct, and easy on the eye. It should have a brief description of who we are and it should have no more than 6 reasons why the client should hire us.

About our online California company. We are not attorneys but legal document assistants who prepare legal documents for probate estate when someone dies with or without a will and assets need to be distributed. We have a flat-fee for Formal Probate of $999 and $699 for Informal Probate. We are an online company and offer our services to the entire state of California in every county. We do everything over the phone and email. The turn around time for us to prepare the initial legal paperwork for the client is within 3-5 business days. We can prepare, file, serve and manage a probate matter from petition to closing. We are not attorneys so our prices are very affordable compare to the attorney.

The company name for the website will be www.velmarhollow.com, The Velmar Hollow Group.

I do not have a logo yet. The colors of the website should be easy on the eye and calming. THE SITE SHOULD BE SIMPLE AND STRAIGHT TO THE POINT. EASY TO NAVIGATE.

The company phone number should be very visible and should stand out to the client. It should also be clickable and ready to dial for smartphone users.

I do not want a contact form on the homepage. THE MAIN THING IS FOR THE POTENTIAL CLIENT TO CALL OUR OFFICE TO SIGN UP.

I do like some images of family or people since we are dealing with people who just lost a loved one. Not all the images have to be of people.

The site should not look like we practice law or that people can mistake us for attorneys.

Target Market(s)

People who just lost a loved one who had property, assets, in California but died with or without a will or trust. This is for people looking to hire non-attorneys.

Coding

Coded - Design and coding required

Font styles to use
Serif

Colors

Designer to choose colors to be used in the design.

Requirements
Must have
• Refer to Project Description.
Nice to have
• The sample images provided is what I am attracted to for the homepage image.
Should not have

```html
<!DOCTYPE html>
<html lang="en">
<head>
<meta charset="utf-8">
<title>Probate | The Velmar Hollow Group</title>
<link rel="stylesheet" href="https://fonts.googleapis.com/css2?family=Crimson+Text:wght@600;700&family=Open+Sans:wght@400;600;700&display=swap">
<style>
:root{
  --teal:#1a6f8c;
  --orange:#f28a1a;
  --ink:#222;
  --body:#444;
  --panel-blue:#1f86a6;
  --panel-orange:#c27a22;
  --hero:#6d6a66;
  --white:#fff;
  --serif:"Crimson Text", Georgia, serif;
  --sans:"Open Sans", Arial, sans-serif;
}
*{margin:0;padding:0;box-sizing:border-box}
html,body{width:677px;height:1200px;overflow:hidden;background:var(--white)}
.page{position:relative;width:677px;height:1200px;overflow:hidden;font-family:var(--sans);color:var(--body)}
.abs{position:absolute}
.top-rule{left:0;top:0;width:677px;height:2px;background:var(--orange)}
.call-pill{left:446px;top:0;width:167px;height:25px;background:var(--orange);border-radius:0 0 14px 14px;color:var(--white);font-size:9.5px;font-weight:700;display:flex;align-items:center;justify-content:center;gap:6px}
.brand{left:56px;top:24px;display:flex;align-items:center;gap:6px;font-family:var(--serif);font-weight:700;font-size:13px;color:var(--teal);letter-spacing:.3px}
.brand-mark{width:10px;height:10px;background:var(--orange)}
.main-nav{left:257px;top:44px;display:flex;gap:22px;font-size:8.5px;font-weight:600;color:var(--ink)}
.hero{left:0;top:70px;width:677px;height:109px;background:linear-gradient(90deg,#6e6a66 0%,#76706a 55%,#8a7e72 100%)}
.hero-title{left:56px;top:106px;font-family:var(--serif);font-weight:700;font-size:31px;color:var(--white);letter-spacing:.5px}
.sec-title{font-family:var(--serif);font-weight:700;color:var(--teal);font-size:19px}
.rule{height:1px;background:var(--teal)}
.about-title{left:56px;top:236px}
.about-rule{left:56px;top:266px;width:52px}
.about-text{left:56px;top:281px;width:314px;font-size:7.6px;line-height:12.7px;text-align:justify}
.about-text p+p{margin-top:9px}
.about-photo{left:386px;top:236px;width:235px;height:175px;border-radius:3px;background:linear-gradient(135deg,#c7c5bb,#8fa67a 55%,#5a7a5a)}
.feature-photo{left:36px;top:438px;width:184px;height:319px;background:linear-gradient(180deg,#f3f1ef 0%,#e7e2dc 45%,#6f8eb1 80%,#4e6f98 100%);border-radius:40% 40% 0 0}
.features{left:251px;top:466px;width:368px}
.feature{margin-bottom:18px}
.feature h3{font-family:var(--serif);font-weight:700;font-size:13.5px;color:var(--teal);letter-spacing:.3px;margin-bottom:5px}
.feature p{font-size:9px;line-height:13.5px;text-align:justify;color:var(--body)}
.panel{top:757px;width:339px;height:275px;color:var(--white);padding:34px 18px 0 56px}
.panel-blue{left:0;background:linear-gradient(135deg,#1a7fa0,var(--panel-blue) 60%,#2c7e98)}
.panel-orange{left:339px;background:linear-gradient(135deg,#b77322,var(--panel-orange) 60%,#a86a20);padding-left:17px}
.panel h2{font-family:var(--serif);font-weight:700;font-size:19px;letter-spacing:.3px}
.panel .rule{width:61px;background:var(--white);margin:9px 0 20px}
.panel p{font-size:8px;font-weight:600;line-height:13.4px;text-align:justify;margin-bottom:12px}
.btn{display:inline-block;margin-top:7px;border:1.5px solid var(--white);padding:8px 6px;font-size:9px;font-weight:700;color:var(--white)}
.foot-nav{left:0;top:1072px;width:677px;display:flex;justify-content:center;gap:14px;font-size:8.5px;font-weight:600;color:var(--ink)}
.foot-nav span.sep{font-weight:400}
.contacts{left:0;top:1113px;width:677px;display:flex;justify-content:center;gap:24px;font-size:12px;color:var(--ink)}
.contact{display:flex;align-items:center;gap:8px}
.foot-rule{left:56px;top:1159px;width:565px;height:1px;background:#333}
.copyright{left:0;top:1174px;width:677px;text-align:center;font-size:8px;font-weight:600;color:var(--ink)}
</style>
</head>
<body>
<div class="page">
  <div class="abs top-rule"></div>
  <div class="abs call-pill">
    <svg width="9" height="9" viewBox="0 0 10 10"><rect width="10" height="10" rx="2" fill="#fff"/><path d="M3 2.5l1 1.5-.6.8c.5 1 1 1.5 1.9 1.9l.8-.6 1.5 1-.6 1.2C4.8 8.2 1.8 5.2 1.9 3.1z" fill="#f28a1a"/></svg>
    Call Us At: +180 447 9162
  </div>
  <div class="abs brand"><span class="brand-mark"></span>THE VELMAR HOLLOW GROUP</div>
  <nav class="abs main-nav"><span>HOME</span><span>ABOUT</span><span>PROBATE</span><span>PROCESS</span><span>FAQ</span><span>CONTACT US</span><span>BLOG</span></nav>

  <div class="abs hero" role="img" aria-label="Photo of a mother embracing two children"></div>
  <h1 class="abs hero-title">PROBATE</h1>

  <h2 class="abs sec-title about-title">VELMAR HOLLOW</h2>
  <div class="abs rule about-rule"></div>
  <div class="abs about-text">
    <p>About our online California company. We are not attorneys but legal document assistants who prepare legal documents for probate estate when someone dies with or without a will and assets need to be distributed. We have a flat-fee for Formal Probate of $999 and $699 for Informal Probate. We are an online company and offer our services to the entire state of California in every county.</p>
    <p>We do everything over the phone and email. The turn around time for us to prepare the initial legal paperwork for the client is within 3-5 business days. We can prepare, file, serve and manage a probate matter from petition to closing. We are not attorneys so our prices are very affordable compare to the attorney.</p>
  </div>
  <div class="abs about-photo" role="img" aria-label="Photo of a mother comforting her young son"></div>

  <div class="abs feature-photo" role="img" aria-label="Photo of a mother holding her daughter"></div>
  <div class="abs features">
    <div class="feature"><h3>NEMO ENIM IPSAM</h3><p>Sed ut perspiciatis unde omnis iste natus error sit voluptatem accusantium doloremque laudantium.</p></div>
    <div class="feature"><h3>TOTAM REM APERIAM</h3><p>Sed ut perspiciatis unde omnis iste natus error sit voluptatem accusantium doloremque laudantium.</p></div>
    <div class="feature"><h3>RATIONE VOLUPTATEM</h3><p>Sed ut perspiciatis unde omnis iste natus error sit voluptatem accusantium doloremque laudantium.</p></div>
    <div class="feature"><h3>VOLUPTATEM ACCUSANTIUM</h3><p>Sed ut perspiciatis unde omnis iste natus error sit voluptatem accusantium doloremque laudantium.</p></div>
  </div>

  <section class="abs panel panel-blue" role="img" aria-label="Blue-tinted photo of hands signing documents">
    <h2>WHAT WE DO</h2><div class="rule"></div>
    <p>Sed ut perspiciatis unde omnis iste natus error sit voluptatem accusantium doloremque laudantium, totam rem aperiam, eaque ipsa quae ab illo inventore veritatis et quasi architecto beatae.</p>
    <p>Nemo enim ipsam voluptatem quia voluptas sit aspernatur aut odit aut fugit, sed quia consequuntur magni dolores eos qui ratione voluptatem.</p>
    <span class="btn">READ MORE</span>
  </section>
  <section class="abs panel panel-orange" role="img" aria-label="Orange-tinted photo of a hand writing with a pen">
    <h2>WHO WE ARE</h2><div class="rule"></div>
    <p>Sed ut perspiciatis unde omnis iste natus error sit voluptatem accusantium doloremque laudantium, totam rem aperiam, eaque ipsa quae ab illo inventore veritatis et quasi architecto beatae.</p>
    <p>Nemo enim ipsam voluptatem quia voluptas sit aspernatur aut odit aut fugit, sed quia consequuntur magni dolores eos qui ratione voluptatem.</p>
    <span class="btn">READ MORE</span>
  </section>

  <nav class="abs foot-nav"><span>HOME</span><span class="sep">|</span><span>ABOUT</span><span class="sep">|</span><span>PROBATE</span><span class="sep">|</span><span>PROCESS</span><span class="sep">|</span><span>FAQ</span><span class="sep">|</span><span>CONTACT US</span><span class="sep">|</span><span>BLOG</span></nav>
  <div class="abs contacts">
    <div class="contact">
      <svg width="25" height="25" viewBox="0 0 26 26"><circle cx="13" cy="13" r="12" fill="none" stroke="#222" stroke-width="1.3"/><path d="M9.5 7.5l2 2.6-1 1.3c.8 1.7 1.9 2.8 3.4 3.6l1.3-1 2.6 2-1 2c-4 .2-8.4-4.2-8.3-8.5z" fill="#222"/></svg>
      +180 447 9162
    </div>
    <div class="contact">
      <svg width="25" height="25" viewBox="0 0 26 26"><circle cx="13" cy="13" r="12" fill="none" stroke="#222" stroke-width="1.3"/><rect x="7.5" y="9" width="11" height="8" rx="1" fill="none" stroke="#222" stroke-width="1.2"/><path d="M7.8 9.5L13 13.5l5.2-4" fill="none" stroke="#222" stroke-width="1.2"/></svg>
      info@velmarhollow.com
    </div>
  </div>
  <div class="abs foot-rule"></div>
  <p class="abs copyright">Copyrights @ 2017 The Velmar Hollow Group. All Rights Reserved.</p>
</div>
</body>
</html>
```